A website for a Maltese Law Firm

Our law firm needs a website to further its business. The site should have a simple yet effective design. We would need the following sections: About us, Practice Areas, About Malta, Contact. These should be further split as follows:

About us: Our firm, Our values, What others say, Offices

Practice Areas: Crimimal, Citizenship & Residence, Sovereign Patron Pathway, Criminal Defence, Civil Litigation, Arbitration and ADR, Commercial and Corporate, Media Law.

About Malta: just one section.

Contact: Just one section

We would also need a news feed at the front of the site to include latest news regarding our cases.

At the bottom we need a section for our Terms and a Privacy Statement.

Our logo is being attached.

Target Market(s)

All clients looking for legal assistance in Malta

Industry/Entity Type

Legal

Coding

Coded - Design and coding required

Number of Pages Required

1 page

Requirements
Must have
• It must be simple yet striking.

```html
<!DOCTYPE html>
<html lang="en">
<head>
<meta charset="utf-8">
<title>Delmare &amp; Serra Advocates</title>
<link rel="stylesheet" href="https://fonts.googleapis.com/css2?family=Cinzel:wght@400;600&family=Raleway:wght@400;500;600;700&display=swap">
<style>
:root{
  --ink:#2f2f2f;
  --text:#6b6b6b;
  --dark:#333333;
  --darker:#2a2a2a;
  --line:#cfcfcf;
  --paper:#ffffff;
  --grey-band:#f0f0f0;
  --news-band:#e4e8ef;
  --footer-text:#c9c9c9;
}
*{box-sizing:border-box;margin:0;padding:0}
html,body{width:1200px;height:2397px;overflow:hidden}
body{position:relative;background:var(--paper);font-family:"Raleway",Arial,sans-serif;color:var(--text)}
.abs{position:absolute}
.serif{font-family:"Cinzel","Times New Roman",serif}

/* top bar */
.topbar{position:absolute;left:0;top:0;width:1200px;height:36px;border-bottom:1px solid #e6e6e6}
.social-top{position:absolute;left:99px;top:0;display:flex}
.social-top span{width:40px;height:36px;border-left:1px solid #e6e6e6;display:flex;align-items:center;justify-content:center}
.social-top span:last-child{border-right:1px solid #e6e6e6}
.social-top i{width:9px;height:9px;border-radius:50%;background:#777;display:block}
.call{position:absolute;left:880px;top:0;width:221px;height:36px;background:var(--dark);color:#fff;font-size:11.5px;letter-spacing:1px;display:flex;align-items:center;justify-content:center;gap:10px}
.call svg{width:18px;height:18px}

/* header */
.header{position:absolute;left:0;top:36px;width:1200px;height:76px}
.logo{position:absolute;left:99px;top:18px;text-align:center}
.logo .name{font-family:"Cinzel",serif;font-size:25px;color:#1c1c1c;letter-spacing:.5px;line-height:1}
.logo .sub{font-family:"Cinzel",serif;font-size:9px;letter-spacing:4px;color:#555;border-top:1px solid #333;border-bottom:1px solid #333;margin-top:3px;line-height:12px}
.nav{position:absolute;right:99px;top:28px;display:flex;gap:36px;font-family:"Cinzel",serif;font-size:13.5px;color:#222}
.nav a{color:inherit;text-decoration:none;padding-bottom:6px}
.nav a.active{border-top:1px solid #222;border-bottom:1px solid #222;padding:3px 4px}

/* hero */
.hero{position:absolute;left:0;top:112px;width:1200px;height:465px;background:linear-gradient(90deg,#0d0d0d 0%,#151515 38%,#3a3936 55%,#6b6a68 75%,#8d8c8a 100%)}
.hero-title{position:absolute;left:100px;top:190px;font-family:"Cinzel",serif;font-size:27px;color:#fff;line-height:34px;letter-spacing:1px}
.hero-btn{position:absolute;left:100px;top:276px;width:229px;height:36px;border:1px solid #fff;color:#fff;font-family:"Cinzel",serif;font-size:12.5px;letter-spacing:.8px;display:flex;align-items:center;justify-content:center}
.arrow{position:absolute;top:200px;width:44px;height:44px}

/* section titles */
.sec-title{position:absolute;width:1200px;text-align:center;font-family:"Cinzel",serif;font-size:25px;color:#666;letter-spacing:1px}
.sec-title b{font-weight:400;color:#222;border-bottom:2px solid #222;border-top:1px solid #222;padding:0 2px}

/* about */
.about-h{position:absolute;left:99px;top:640px;font-family:"Cinzel",serif;font-size:24px;color:#666;letter-spacing:1px}
.about-h b{font-weight:400;color:#222;border-bottom:2px solid #222;border-top:1px solid #222;padding:0 3px;margin-left:8px}
.about-p{position:absolute;left:99px;top:688px;width:590px;font-size:13.4px;line-height:25px}
.btn-dark{position:absolute;width:134px;height:39px;background:var(--dark);color:#fff;font-family:"Cinzel",serif;font-size:12.5px;display:flex;align-items:center;justify-content:center;letter-spacing:.6px}
.feature{position:absolute;left:748px;width:354px;height:96px}
.feature .ico{position:absolute;left:0;top:0;width:96px;height:96px;border:1px solid #cfcfcf;display:flex;align-items:center;justify-content:center}
.feature h3{position:absolute;left:114px;top:4px;font-family:"Cinzel",serif;font-weight:400;font-size:17px;color:#222}
.feature p{position:absolute;left:114px;top:30px;font-size:12px;line-height:19px;width:240px}

/* practice */
.practice{position:absolute;left:0;top:946px;width:1200px;height:350px;background:linear-gradient(100deg,#efefef 0%,#f1f1f1 55%,#e8e8e8 100%)}
.area{position:absolute;top:117px;width:152px}
.area .box{width:152px;height:97px;border:1px solid #cdcdcd;background:#f5f5f5;display:flex;align-items:center;justify-content:center}
.area .lbl{height:52px;display:flex;align-items:center;justify-content:center;text-align:center;font-family:"Cinzel",serif;font-size:12.5px;color:#222;line-height:14px;border-bottom:1px solid #9a9a9a}
.dots{position:absolute;top:297px;left:581px;display:flex;gap:5px}
.dots i{width:8px;height:8px;border-radius:50%;border:1px solid #999;display:block}
.dots i.on{background:#888}

/* malta */
.malta-frame{position:absolute;left:99px;top:1401px;width:420px;height:245px;border:1px solid #d6d6d6;background:#fff}
.malta-img{position:absolute;left:117px;top:1419px;width:420px;height:248px;background:linear-gradient(180deg,#7aa6d6 0%,#b7c6dc 35%,#d69b5b 55%,#4e78b8 72%,#8fb4e4 100%)}
.malta-p{position:absolute;left:567px;top:1401px;width:534px;font-size:13.4px;line-height:25.5px}
.bullets{position:absolute;left:567px;top:1565px;width:534px;list-style:none}
.bullets li{position:relative;padding-left:23px;font-size:13px;font-weight:600;color:#222;line-height:17px;margin-bottom:16px}
.bullets svg{position:absolute;left:0;top:3px;width:13px;height:11px}

/* news */
.news{position:absolute;left:0;top:1721px;width:1200px;height:454px;background:linear-gradient(90deg,#e7eaf0 0%,#dfe4ec 60%,#e6e8ee 100%)}
.post{position:absolute;top:113px;width:479px}
.post .img{position:relative;width:479px;height:173px}
.post .date{position:absolute;left:0;bottom:0;width:60px;height:60px;background:#1e1e1e;color:#fff;text-align:center;padding-top:8px}
.post .date b{display:block;font-size:21px;font-weight:600;line-height:22px}
.post .date span{font-size:14px}
.post p{margin-top:20px;font-size:13.4px;line-height:24px;width:470px}
.btn-line{margin-top:15px;width:126px;height:37px;border:1px solid #444;font-family:"Cinzel",serif;font-size:12.5px;color:#333;display:flex;align-items:center;justify-content:center}

/* footer */
.footer{position:absolute;left:0;top:2175px;width:1200px;height:222px;background:var(--dark);color:var(--footer-text)}
.flogo{position:absolute;left:121px;top:83px;text-align:center}
.flogo .name{font-family:"Cinzel",serif;font-size:22px;color:#fff;line-height:1}
.flogo .sub{font-family:"Cinzel",serif;font-size:8px;letter-spacing:4px;border-top:1px solid #ccc;border-bottom:1px solid #ccc;margin-top:3px;line-height:11px;color:#ddd}
.copy{position:absolute;left:99px;top:137px;font-size:11px}
.fhead{position:absolute;top:46px;font-family:"Cinzel",serif;font-size:16.5px;color:#fff;letter-spacing:1.5px;padding-bottom:6px;border-bottom:1px solid #777}
.flink{position:absolute;font-size:11.5px;padding-left:18px}
.flink svg{position:absolute;left:0;top:2px;width:10px;height:9px}
.fsocial{position:absolute;left:594px;top:172px;display:flex;gap:12px}
.fsocial i{width:11px;height:11px;border-radius:50%;background:#ddd;display:block}
.signup{position:absolute;left:799px;top:92px;width:302px;height:34px;display:flex}
.signup .field{flex:1;background:#4a4a4a;color:#bbb;font-style:italic;font-size:11.5px;display:flex;align-items:center;padding-left:14px}
.signup .go{width:46px;background:#e2e2e2;display:flex;align-items:center;justify-content:center}
.finfo{position:absolute;font-size:11.5px;display:flex;align-items:center;gap:9px}
.finfo svg{width:12px;height:12px}
</style>
</head>
<body>

<div class="topbar">
  <div class="social-top"><span><i></i></span><span><i></i></span><span><i></i></span></div>
  <div class="call">
    <svg viewBox="0 0 20 20"><circle cx="10" cy="10" r="9" fill="none" stroke="#fff" stroke-width="1"/><path d="M6.5 5.5l2 2-1 1.5c.7 1.5 1.8 2.6 3.3 3.3l1.5-1 2 2-1.3 1.3c-3.6-.3-7.5-4.2-7.8-7.8z" fill="#fff"/></svg>
    CALL US : (356) 2000 4810
  </div>
</div>

<header class="header">
  <div class="logo"><div class="name">DELMARE &amp; SERRA</div><div class="sub">ADVOCATES</div></div>
  <nav class="nav">
    <a class="active">Home</a><a>About us</a><a>Practice Areas</a><a>About Malta</a><a>Contact</a>
  </nav>
</header>

<section class="hero" role="img" aria-label="Photograph of a man with his hands handcuffed behind his back">
  <svg class="arrow" style="left:24px" viewBox="0 0 44 44"><path d="M18 4H4v36h14" fill="none" stroke="#666" stroke-width="1.5"/><path d="M40 22H12m7-7l-7 7 7 7" fill="none" stroke="#777" stroke-width="1.5"/></svg>
  <svg class="arrow" style="right:24px" viewBox="0 0 44 44"><path d="M26 4h14v36H26" fill="none" stroke="#999" stroke-width="1.5"/></svg>
  <div class="hero-title">The Greatest &amp; Stongest<br>Firm You Can Trust</div>
  <div class="hero-btn">Request A Free Consultant</div>
</section>

<!-- about -->
<h2 class="about-h">About<b>Delmare &amp; Serra</b></h2>
<p class="about-p">Lorem ipsum dolor sit amet, consectetuer adipiscing elit, sed diam nonummy nibh euismod tincidunt ut laoreet dolore magna aliquam erat volutpat. Ut wisi enim ad minim veniam, quis nostrud exerci tation ullamcorper suscipit lobortis nisl ut aliquip ex ea commodo consequat. Duis autem vel eum iriure dolor in hendrerit in vulputate velit esse molestie consequat, vel illum dolore eu feugiat nulla facilisis at vero eros et accumsan et iusto odio dignissim qui blandit praesent luptatum &nbsp;te feugait nulla facilisi.</p>
<div class="btn-dark" style="left:99px;top:856px">Read More</div>

<div class="feature" style="top:663px">
  <div class="ico"><svg width="64" height="40" viewBox="0 0 64 40"><path d="M2 10l10-4 8 16-8 4zM62 10l-10-4-8 16 8 4z" fill="#222"/><path d="M18 11l10-3 8 4 8-2 4 10-10 10-6-1-12-10z" fill="#222"/><path d="M30 12l-6 6 3 2 7-5" fill="#fff"/></svg></div>
  <h3>Our Values</h3>
  <p>Artis nisl ut aliquip ex ea commodoll eros et accumsan o digniss qui nulla facilis...[+]</p>
</div>
<div class="feature" style="top:791px">
  <div class="ico"><svg width="52" height="48" viewBox="0 0 52 48"><path d="M26 2L2 14h48z" fill="#222"/><rect x="4" y="16" width="44" height="4" fill="#222"/><rect x="8" y="22" width="6" height="16" fill="#222"/><rect x="18" y="22" width="6" height="16" fill="#222"/><rect x="28" y="22" width="6" height="16" fill="#222"/><rect x="38" y="22" width="6" height="16" fill="#222"/><rect x="2" y="40" width="48" height="6" fill="#222"/></svg></div>
  <h3>Our firm</h3>
  <p>Artis nisl ut aliquip ex ea commodoll eros et accumsan o digniss qui nulla facilis...[+]</p>
</div>

<!-- practice areas -->
<section class="practice">
  <h2 class="sec-title" style="top:42px;left:0">Practice <b>Areas</b></h2>
  <div class="area" style="left:99px">
    <div class="box"><svg width="60" height="50" viewBox="0 0 60 50"><circle cx="16" cy="32" r="12" fill="none" stroke="#222" stroke-width="4"/><circle cx="44" cy="22" r="12" fill="none" stroke="#222" stroke-width="4"/><rect x="10" y="8" width="10" height="10" fill="#222"/><path d="M24 26l10-6" stroke="#222" stroke-width="3"/></svg></div>
    <div class="lbl">Criminal Law</div>
  </div>
  <div class="area" style="left:312px">
    <div class="box"><svg width="52" height="46" viewBox="0 0 52 46"><path d="M26 2L2 22h7v22h12V30h10v14h12V22h7z" fill="#222"/></svg></div>
    <div class="lbl">Citizenship &amp;<br>Residence</div>
  </div>
  <div class="area" style="left:524px">
    <div class="box"><svg width="46" height="50" viewBox="0 0 46 50"><rect x="4" y="2" width="38" height="46" rx="3" fill="none" stroke="#222" stroke-width="3"/><circle cx="23" cy="20" r="9" fill="none" stroke="#222" stroke-width="3"/><rect x="12" y="36" width="22" height="3" fill="#222"/></svg></div>
    <div class="lbl">Sovereign Patron<br>Pathway</div>
  </div>
  <div class="area" style="left:737px">
    <div class="box"><svg width="56" height="50" viewBox="0 0 56 50"><rect x="12" y="4" width="22" height="12" transform="rotate(40 23 10)" fill="#222"/><path d="M26 20l20 16-4 4-20-16z" fill="#222"/><rect x="4" y="42" width="26" height="5" fill="#222"/></svg></div>
    <div class="lbl">Civil<br>Litigation</div>
  </div>
  <div class="area" style="left:949px">
    <div class="box"><svg width="52" height="50" viewBox="0 0 52 50"><rect x="10" y="2" width="32" height="28" rx="2" fill="#222"/><circle cx="26" cy="13" r="5" fill="#fff"/><rect x="18" y="20" width="16" height="6" rx="3" fill="#fff"/><rect x="4" y="34" width="44" height="4" fill="#222"/><rect x="2" y="42" width="48" height="5" fill="#222"/></svg></div>
    <div class="lbl">Arbitration<br>and ADR</div>
  </div>
  <div class="dots"><i class="on"></i><i></i><i></i></div>
</section>

<!-- about malta -->
<h2 class="sec-title" style="top:1340px;left:0">About <b>Malta</b></h2>
<div class="malta-frame"></div>
<div class="malta-img" role="img" aria-label="Photograph of the Valletta waterfront lit up at dusk"></div>
<p class="malta-p">Aeuismod tincidunt ut laoreet dolore magna aliquam erat volutpat. Ut wisi enim ad minim veniam, quis nostrud exerci tation ullamcorper suscipit lobortis nisl ut aliquip ex ea commodo consequat. Duis autem vel eum iriure dolor in hendrerit in vulputate velit esse molestie consequat, vel illum dolore eu feugiat nulla facilisis at vero eros et accumsan et iusto odio dignissim qui blandit praesent luptatum &nbsp;te feugait nulla facilisi.</p>
<ul class="bullets">
  <li><svg viewBox="0 0 13 11"><path d="M1 5.5h9M6 1.5l4.5 4-4.5 4" fill="none" stroke="#333" stroke-width="1.3"/></svg>Duis autem vel eum iriure dolor in hendrerit in vulputate vl conseqt,molestie consequat vel illum dolore.</li>
  <li><svg viewBox="0 0 13 11"><path d="M1 5.5h9M6 1.5l4.5 4-4.5 4" fill="none" stroke="#333" stroke-width="1.3"/></svg>Ut wisi enim ad minim veniam, qui nostrud exeullamcorper suscipit lobortis .</li>
  <li><svg viewBox="0 0 13 11"><path d="M1 5.5h9M6 1.5l4.5 4-4.5 4" fill="none" stroke="#333" stroke-width="1.3"/></svg>Aulputate velit esse molestie consequat, vel illum dolore eu feugiat.</li>
</ul>

<!-- news -->
<section class="news">
  <h2 class="sec-title" style="top:35px;left:0">Latest <b>News</b></h2>
  <article class="post" style="left:99px">
    <div class="img" role="img" aria-label="Photograph of a man reading papers at a desk" style="background:linear-gradient(120deg,#1d2228 0%,#3b4450 50%,#6a5a4a 100%)">
      <div class="date"><b>08</b><span>JUNE</span></div>
    </div>
    <p>lobortis nisl ut aliquip ex ea commodo consequat. Duis autem vel eum iriure dolor in hendrerit inilore eu feugiat nulla facilisis at vero..</p>
    <div class="btn-line">Read More</div>
  </article>
  <article class="post" style="left:622px">
    <div class="img" role="img" aria-label="Photograph of a wooden gavel resting on an open book" style="background:linear-gradient(110deg,#d8d2c8 0%,#b88a5a 45%,#7a4a22 70%,#e8e4de 100%)">
      <div class="date"><b>08</b><span>JUNE</span></div>
    </div>
    <p>lobortis nisl ut aliquip ex ea commodo consequat. Duis autem vel eum iriure dolor in hendrerit in vulpue molestie ct, velo..</p>
    <div class="btn-line">Read More</div>
  </article>
</section>

<!-- footer -->
<footer class="footer">
  <div class="flogo"><div class="name">DELMARE &amp; SERRA</div><div class="sub">ADVOCATES</div></div>
  <div class="copy">Copyright © 2016 Delmare &amp; Serra. All rights reserved.</div>

  <div class="fhead" style="left:465px">Navigation</div>
  <div class="flink" style="left:460px;top:93px"><svg viewBox="0 0 10 9"><path d="M1 4.5L5 1l4 3.5L5 8z" fill="none" stroke="#ccc"/></svg>Home</div>
  <div class="flink" style="left:460px;top:132px"><svg viewBox="0 0 10 9"><path d="M1 4.5L5 1l4 3.5L5 8z" fill="none" stroke="#ccc"/></svg>About us</div>
  <div class="flink" style="left:460px;top:172px"><svg viewBox="0 0 10 9"><path d="M1 4.5L5 1l4 3.5L5 8z" fill="none" stroke="#ccc"/></svg>Practice Areas</div>
  <div class="flink" style="left:592px;top:93px"><svg viewBox="0 0 10 9"><path d="M1 4.5L5 1l4 3.5L5 8z" fill="none" stroke="#ccc"/></svg>About Malta</div>
  <div class="flink" style="left:592px;top:132px"><svg viewBox="0 0 10 9"><path d="M1 4.5L5 1l4 3.5L5 8z" fill="none" stroke="#ccc"/></svg>Contact Us</div>
  <div class="fsocial"><i></i><i></i><i></i><i></i></div>

  <div class="fhead" style="left:799px">Newsletter</div>
  <div class="signup">
    <div class="field">Enter Your Email</div>
    <div class="go"><svg width="20" height="18" viewBox="0 0 20 18"><path d="M1 8L19 1l-4 16-5-6zM10 11l9-10" fill="none" stroke="#333" stroke-width="1.4"/></svg></div>
  </div>
  <div class="finfo" style="left:808px;top:145px"><svg viewBox="0 0 12 12"><path d="M6 1a3.5 3.5 0 013.5 3.5C9.5 7 6 11 6 11S2.5 7 2.5 4.5A3.5 3.5 0 016 1z" fill="#eee"/><circle cx="6" cy="4.5" r="1.3" fill="#333"/></svg>58 Marina Street, Sliema</div>
  <div class="finfo" style="left:808px;top:172px"><svg viewBox="0 0 12 12"><path d="M2 1.5l2.5 2.5-1 1.3c.7 1.4 1.8 2.5 3.2 3.2l1.3-1L10.5 10 9 11.3C5 11 1 7 .7 3z" fill="#eee"/></svg>(356) 2000 4810</div>
  <div class="finfo" style="left:945px;top:172px"><svg viewBox="0 0 12 12"><rect x="1" y="2.5" width="10" height="7" fill="#eee"/><path d="M1 2.5l5 4 5-4" fill="none" stroke="#333"/></svg>info@delmareserra.com</div>
</footer>

</body>
</html>
```